Valdane Companies Business Card Design

We need a new business card for our Private Equity Real Estate Development firm, “Valdane” and our EB-5 regional center “Thornmere Regional Center” on one card. We prefer a design that is simple, elegant, and represents the luxury products we design and build as well as the financial security and stability our successful history has produced. We are an industry leader in our field and 3rd generation family business that has evolved into an institutional quality investment platform. Considered design size is standard business card dimensions (3.5 x 2 inches with an additional 1/8 inch space for design elements or backgrounds that extend beyond the finished size of your piece.

Target Market(s)

• High net worth individuals
• Highly skilled technical workers and physicians in the US seeking investment-based immigration opportunities
• Sophisticated private equity investors
• Intermediary partners include domestic attorneys and investment brokers, as well as international agent networks
• US real estate developers

Industry/Entity Type

Finance

Contact Information for Business Card

(Providing placeholder info for personal information, please design for longer character spaces, longer names and addresses etc..)
• Logo for Valdane
• Logo for Thornmere Regional Center
• Full name: Marcus Valdane
• Job title: CEO
• Email address: mvaldane@valdanecompanies.com
• Cell phone number: +1.555.314.2287
• Office number +1.555.628.4410
• Office address: Larkfield Court 5, 4817 Vista Orilla, Cresthaven, CA.
• Website: www.valdanecompanies.com

Font styles to use
Serif
Sans Serif

Colors
ec1f27
ffffff
000000

Requirements
Must have
• • Logo for Valdane
• • Logo for Thornmere Regional Center
• - Use rounded corners
• (See .ai file included for logos)
Nice to have
• • Simple, elegant design
• • Aesthetically compatible with our website design (www.valdanecompanies.com)
• • Color palette including but not limited to white, black, and red (as per logos)
Should not have
• - Not too much red color
• - Do not stack both logos on top of each other

```html
<!DOCTYPE html>
<html lang="en">
<head>
<meta charset="utf-8">
<title>Valdane Companies Business Card</title>
<link rel="stylesheet" href="https://fonts.googleapis.com/css2?family=Cinzel:wght@700&family=Libre+Baskerville:wght@400;700&family=Roboto:wght@400&display=swap">
<style>
  :root {
    --backdrop: #2b2b2b;
    --paper: #f4f4f4;
    --crimson: #9b1639;
    --crimson-dark: #6c0d29;
    --crimson-light: #b01f4e;
    --ink: #555555;
    --ink-dark: #1a1a1a;
    --rule-grey: #a9a9a9;
    --white: #ffffff;
  }
  * { margin: 0; padding: 0; box-sizing: border-box; }
  html, body { width: 1200px; height: 960px; overflow: hidden; }
  body { background: var(--backdrop); position: relative; font-family: "Roboto", Arial, sans-serif; }

  .card { position: absolute; width: 600px; height: 343px; border-radius: 4px; overflow: hidden; }
  .card-front { left: 314px; top: 113px; background: var(--paper); }
  .card-back {
    left: 311px; top: 472px;
    background: radial-gradient(ellipse 60% 75% at 50% 38%, var(--crimson-light) 0%, var(--crimson) 45%, var(--crimson-dark) 100%);
  }

  .center-mark { position: absolute; left: 43px; top: 50px; display: flex; align-items: center; gap: 12px; }
  .center-mark .mark-square { width: 50px; height: 50px; background: var(--crimson); }
  .center-mark .mark-name { font-family: "Cinzel", Georgia, serif; font-weight: 700; color: var(--crimson); line-height: 1; }
  .center-mark .mark-name .line-main { display: block; font-size: 31px; }
  .center-mark .mark-name .line-sub { display: block; font-size: 10.5px; letter-spacing: 3.6px; margin-top: 5px; }

  .address { position: absolute; left: 40px; top: 159px; font-size: 14px; line-height: 18px; color: var(--ink); font-style: normal; }

  .contact-list { position: absolute; left: 40px; top: 225px; list-style: none; font-size: 14px; color: var(--ink); }
  .contact-list li { display: flex; align-items: center; height: 19.5px; }
  .contact-list svg { width: 13px; height: 13px; margin-right: 9px; fill: var(--crimson); }

  .person { position: absolute; right: 37px; top: 158px; text-align: right; }
  .person .person-name { font-family: "Libre Baskerville", Georgia, serif; font-weight: 700; font-size: 20px; color: var(--crimson); text-transform: uppercase; line-height: 1.1; }
  .person .person-title { font-family: "Libre Baskerville", Georgia, serif; font-size: 14px; color: var(--ink-dark); line-height: 1.2; }

  .footer-band { position: absolute; left: 0; bottom: 0; width: 600px; height: 40px; }
  .website { position: absolute; right: 36px; bottom: 11px; font-size: 14px; color: var(--white); }

  .capital-mark { position: absolute; left: 0; right: 0; top: 88px; text-align: center; color: var(--white); font-family: "Cinzel", Georgia, serif; font-weight: 700; }
  .capital-mark .mark-square { width: 72px; height: 72px; background: var(--white); margin: 0 auto 28px; }
  .capital-mark .line-main { display: block; font-size: 44px; line-height: 1; }
  .capital-mark .line-sub { display: block; font-size: 14px; letter-spacing: 5px; margin-top: 8px; }
</style>
</head>
<body>

  <section class="card card-front">
    <div class="center-mark">
      <div class="mark-square"></div>
      <div class="mark-name">
        <span class="line-main">Thornmere</span>
        <span class="line-sub">Regional Center</span>
      </div>
    </div>

    <address class="address">
      Larkfield Court 5<br>
      4817 Vista Orilla<br>
      Cresthaven, CA.
    </address>

    <ul class="contact-list">
      <li>
        <svg viewBox="0 0 24 24"><path d="M6.6 10.8a15.1 15.1 0 0 0 6.6 6.6l2.2-2.2c.3-.3.7-.4 1-.2 1.1.4 2.3.6 3.6.6.6 0 1 .4 1 1V20c0 .6-.4 1-1 1A17 17 0 0 1 3 4c0-.6.4-1 1-1h3.5c.6 0 1 .4 1 1 0 1.3.2 2.5.6 3.6.1.3 0 .7-.2 1z"/></svg>
        +1.555.628.4410
      </li>
      <li>
        <svg viewBox="0 0 24 24"><path d="M7 1h10a2 2 0 0 1 2 2v18a2 2 0 0 1-2 2H7a2 2 0 0 1-2-2V3a2 2 0 0 1 2-2zm0 3v14h10V4zm5 15.5a1.2 1.2 0 1 0 0 2.4 1.2 1.2 0 0 0 0-2.4z"/></svg>
        +1.555.314.2287
      </li>
      <li>
        <svg viewBox="0 0 24 24"><path d="M2 5h20v14H2zm2 2v.5l8 5 8-5V7zm0 2.9V17h16V9.9l-8 5z"/></svg>
        mvaldane@valdanecompanies.com
      </li>
    </ul>

    <div class="person">
      <div class="person-name">Marcus Valdane</div>
      <div class="person-title">CEO</div>
    </div>

    <svg class="footer-band" viewBox="0 0 600 40" preserveAspectRatio="none">
      <defs>
        <linearGradient id="bandFill" x1="0" y1="0" x2="0" y2="1">
          <stop offset="0" stop-color="#a81a44"/>
          <stop offset="1" stop-color="#7c1030"/>
        </linearGradient>
      </defs>
      <path d="M0 15 H318 Q326 15 332 9 Q340 1 352 1 H600 V40 H0 Z" fill="var(--rule-grey)"/>
      <path d="M0 28 H310 Q322 28 330 17 Q340 0 356 0 H600 V40 H0 Z" fill="url(#bandFill)"/>
    </svg>
    <div class="website">www.valdanecompanies.com</div>
  </section>

  <section class="card card-back">
    <div class="capital-mark">
      <div class="mark-square"></div>
      <span class="line-main">Valdane</span>
      <span class="line-sub">CAPITAL</span>
    </div>
  </section>

</body>
</html>
```